Business card design for a dynamic IT consulting company

We need a business card design for a young firm, specialized in the Telecommunications/Consulting industry. The name of the company is Quindor and Partners Business Consulting Ltd. (Short name: Quindor and Partnes)
Quindor = solve read reverse, so we aim to be uncomplicated and solution-oriented. The small pipe in our logo is also related to the word solve. So we need a new business card design, which is simple, eye catching and something non traditional (I would probably prefer a square shaped design rather than a rectangle, but open for suggestions). Attached our logo.

Target Market(s)

Usually our customers are Tier1 Telecoms providers (Q-Netra, Palorix, etc) and their executives.

Industry/Entity Type

Business

Contact Information for Business Card

Name: Bence Tolnavari
Email: b.tolnavari@quindor.hu
Web: www.quindor.hu
Mobile: +36 30 518 2769
Title: Managing Director

Optional:
Company name: Quindor and Partners Ltd.
Address: 1087 Budapest, Tolvenka str. 28/C, Hungary

Font styles to use
Other font styles liked:
• helveticaneue_medium, Prime Regular are used now.

Colors

Designer to choose colors to be used in the design.

Requirements
Must have
• I would like to have a 2 sided design.
Nice to have
• I thought if we make the logo a bit bigger (without the company name), that could go to the back with the company name below. I though, if the pipe in the logo is somehow touchable on the business card, would be nice and unique.

```html
<!DOCTYPE html>
<html lang="en">
<head>
<meta charset="utf-8">
<title>Quindor &amp; Partners — Business Card</title>
<link href="https://fonts.googleapis.com/css2?family=Saira:wght@400;500&family=Arimo:wght@400&display=swap" rel="stylesheet">
<style>
  :root {
    --backdrop: #2b2623;
    --card: #1b1b1c;
    --card-edge: #111112;
    --ink: #f2f2f2;
    --emboss: #4a4a4c;
    --magenta: #c0238f;
    --blue: #1a9ad6;
    --muted: #d8d8d8;
  }
  * { box-sizing: border-box; margin: 0; padding: 0; }
  html, body {
    width: 1200px; height: 780px; overflow: hidden;
    background: var(--backdrop);
  }
  .canvas {
    position: relative; width: 1200px; height: 780px;
    display: flex; align-items: center; justify-content: center; gap: 40px;
  }
  .card {
    position: relative; width: 540px; height: 350px;
    background: var(--card);
    border: 1px solid var(--card-edge);
    border-radius: 22px;
    overflow: hidden;
  }

  /* Back side */
  .card-back { display: flex; align-items: center; justify-content: center; }
  .back-wordmark {
    font-family: "Saira", sans-serif; font-weight: 500;
    font-size: 44px; letter-spacing: 0.5px;
    color: var(--emboss);
  }

  /* Front side */
  .front-wordmark {
    position: absolute; left: 34px; top: 30px;
    font-family: "Saira", sans-serif; font-weight: 500;
    font-size: 38px; color: var(--ink); letter-spacing: 0.3px;
  }
  .person { position: absolute; left: 34px; top: 140px; }
  .person-name {
    font-family: "Saira", sans-serif; font-weight: 500;
    font-size: 20px; color: var(--ink); line-height: 1.1;
  }
  .person-title {
    font-family: "Arimo", sans-serif; font-size: 14px;
    color: var(--magenta); margin-top: 2px;
  }
  .divider {
    position: absolute; left: 34px; right: 0; top: 196px; height: 2px;
    background: linear-gradient(to right, var(--blue) 0 48%, var(--magenta) 48% 100%);
  }
  .title-rule {
    position: absolute; left: 34px; top: 188px; width: 150px; height: 2px;
    background: var(--blue);
  }
  .contacts {
    position: absolute; left: 34px; top: 212px;
    list-style: none;
    font-family: "Arimo", sans-serif; font-size: 14px; color: var(--muted);
  }
  .contacts li { display: flex; align-items: center; gap: 9px; height: 21px; }
  .contacts svg { width: 13px; height: 13px; flex: none; }
  .address {
    position: absolute; right: 30px; bottom: 26px; text-align: right;
    font-family: "Arimo", sans-serif; font-size: 15px; line-height: 1.3;
    color: var(--ink);
  }
</style>
</head>
<body>
<main class="canvas">
  <section class="card card-back" aria-label="Card back">
    <div class="back-wordmark">Quindor &amp; Partners</div>
  </section>

  <section class="card card-front" aria-label="Card front">
    <div class="front-wordmark">Quindor &amp; Partners</div>

    <div class="person">
      <div class="person-name">Bence Tolnavari</div>
      <div class="person-title">Managing Director</div>
    </div>
    <div class="divider"></div>

    <ul class="contacts">
      <li>
        <svg viewBox="0 0 13 13" aria-hidden="true"><rect x="3" y="1" width="7" height="11" rx="1" fill="none" stroke="var(--magenta)" stroke-width="1.4"/></svg>
        +36 30 518 2769
      </li>
      <li>
        <svg viewBox="0 0 13 13" aria-hidden="true"><rect x="1" y="3" width="11" height="8" fill="var(--ink)"/><path d="M1 3 L6.5 7.5 L12 3" fill="none" stroke="var(--card)" stroke-width="1"/></svg>
        b.tolnavari@quindor.hu
      </li>
      <li>
        <svg viewBox="0 0 13 13" aria-hidden="true"><circle cx="6.5" cy="6.5" r="5.5" fill="var(--blue)"/><path d="M1 6.5 H12 M6.5 1 C3.5 4 3.5 9 6.5 12 C9.5 9 9.5 4 6.5 1" fill="none" stroke="var(--card)" stroke-width="0.7"/></svg>
        www.quindor.hu
      </li>
    </ul>

    <address class="address" style="font-style:normal">
      1087 Budapest,<br>
      Tolvenka str. 28/C,<br>
      Hungary
    </address>
  </section>
</main>
</body>
</html>
```